Business Goals Posters for display within company office and factory.

We have three (3) high level business goals we want to display in the office and factory areas of the business.

1. Under the heading of "QUALITY"
"We will have pride and ownership of every product and service delivered to our customers."

2. Under the heading of "PRODUCTIVITY"
"We will put the customer's expectations first and ensure our team is empowered to do so."

3. Under the heading of "SAFETY"
"We will shift our culture to ensure safety is our first thought on every job."

We would like a matching set of posters with these three headings and statements with a background suitable for display in a business environment. The posters will be displayed in sizes from A4 and A2.
The company's logo is Red and Black (see attachment) .
We make Electric and Hydraulic power packs for industrial market.
our website will give you an idea of what we do www.quorvanenergy.com.au

Industry/Entity Type

Power Generation

Colors

Designer to choose colors to be used in the design.

Requirements
Must have
• The posters must use the exact text provided and have the headings listed.
• the three posters must have a common theme. they can be different in back ground but when side by side must look like a set.
• Be suitable for display as A4 and as A2.
Nice to have
• The text needs the be the star, the background needs to draw attention to the poster and the text with out over powering it,
Should not have
• not have photo's of generators or equipment as backgrounds

```html
<!DOCTYPE html>
<html lang="en">
<head>
<meta charset="utf-8">
<title>Quality – Business Goals Poster</title>
<link href="https://fonts.googleapis.com/css2?family=Barlow+Condensed:wght@400;600&family=Yellowtail&display=swap" rel="stylesheet">
<style>
  :root {
    --paper-light: #f1f1f0;
    --paper-mid: #dcdcdb;
    --paper-shade: #c4c4c3;
    --reveal-yellow: #f2b227;
    --reveal-deep: #e49c16;
    --ink: #111111;
    --brand-red: #e0201f;
    --skin-light: #f0c9b0;
    --skin-deep: #c98f74;
  }
  html, body {
    margin: 0;
    padding: 0;
    overflow: hidden;
    background: var(--paper-light);
  }
  .poster {
    position: relative;
    width: 849px;
    height: 1200px;
    overflow: hidden;
    background: var(--paper-light);
  }
  .torn-paper {
    position: absolute;
    inset: 0;
    width: 849px;
    height: 1200px;
  }
  .goal-statement {
    position: absolute;
    left: 392px;
    top: 272px;
    margin: 0;
    width: 300px;
    font-family: "Barlow Condensed", sans-serif;
    font-weight: 400;
    font-size: 44px;
    line-height: 45px;
    letter-spacing: -0.5px;
    color: var(--ink);
  }
  .goal-heading {
    position: absolute;
    left: 262px;
    top: 958px;
    margin: 0;
    font-family: "Yellowtail", cursive;
    font-weight: 400;
    font-size: 132px;
    line-height: 1;
    color: var(--ink);
    transform: rotate(-12deg);
    transform-origin: left bottom;
  }
  .heading-stroke {
    position: absolute;
    left: 0;
    top: 0;
    width: 849px;
    height: 1200px;
    pointer-events: none;
  }
  .writing-hand {
    position: absolute;
    left: 626px;
    top: 923px;
    width: 223px;
    height: 277px;
    background: linear-gradient(200deg, var(--skin-light) 0%, var(--skin-deep) 70%, #8a8f96 100%);
    border-top-left-radius: 120px 90px;
  }
  .brand-name {
    position: absolute;
    left: 28px;
    top: 1128px;
    display: flex;
    align-items: center;
    gap: 10px;
    font-family: "Barlow Condensed", sans-serif;
    font-weight: 600;
    font-size: 30px;
    line-height: 1;
    color: var(--brand-red);
  }
  .brand-mark {
    width: 22px;
    height: 22px;
    background: var(--brand-red);
  }
</style>
</head>
<body>
<main class="poster">
  <svg class="torn-paper" role="img" aria-label="Photograph of white paper torn open to reveal a yellow textured layer beneath" viewBox="0 0 849 1200">
    <defs>
      <linearGradient id="paperTone" x1="0" y1="0" x2="1" y2="1">
        <stop offset="0" stop-color="var(--paper-mid)"/>
        <stop offset="0.45" stop-color="var(--paper-light)"/>
        <stop offset="1" stop-color="var(--paper-shade)"/>
      </linearGradient>
      <linearGradient id="revealTone" x1="0" y1="0" x2="1" y2="1">
        <stop offset="0" stop-color="var(--reveal-yellow)"/>
        <stop offset="1" stop-color="var(--reveal-deep)"/>
      </linearGradient>
    </defs>
    <rect width="849" height="1200" fill="url(#paperTone)"/>
    <polygon points="53,361 743,64 721,849" fill="url(#revealTone)"/>
  </svg>

  <p class="goal-statement">We will have pride and ownership of every product and service delivered to our customers</p>

  <svg class="heading-stroke" viewBox="0 0 849 1200" aria-hidden="true">
    <path d="M330 1150 Q470 1080 628 1018" stroke="var(--ink)" stroke-width="5" fill="none" stroke-linecap="round"/>
  </svg>
  <h1 class="goal-heading">Quality</h1>

  <div class="writing-hand" role="img" aria-label="Photograph of a hand holding a pen, writing the heading"></div>

  <div class="brand-name"><span class="brand-mark"></span>Quorvan Energy</div>
</main>
</body>
</html>
```